Harbor Crestline (Business Card Design)

Need business cards designed. Something modern, chic, and sleek. Mabye the back of the card should be the navy blue that is in the logo and then just the logo on the back.

Target Market(s)

Those in the hotel, office, and renovation industry

Contact Information for Business Card

1. Logo 2. Dorian Fenwick 3. CEO/Founder 4. Phone: (833) HarbCre / (833) 427-2731 5. Email: dorian@theharborcrestline.com 6. Website: www.theharborcrestline.com

Font styles to use
Other font styles liked:
• Look at the logo font and base the font for everything else off of that.

Colors
0054AA
0677BA
7BADD7
CADEEF
E8F1F8

Requirements
Must have
• Colors that are associated in the logo
Nice to have
• Sleek modern clean and chic design.

```html
<!DOCTYPE html>
<html lang="en">
<head>
<meta charset="utf-8">
<title>Harbor Crestline – Business Card</title>
<link href="https://fonts.googleapis.com/css2?family=Montserrat:wght@600;700&family=Open+Sans:wght@400;600&display=swap" rel="stylesheet">
<style>
  :root {
    --stage: #232327;
    --navy: #0d1844;
    --navy-light: #1a2660;
    --gold: #c9a24a;
    --white: #ffffff;
    --muted: #d6dbea;
  }
  * { box-sizing: border-box; margin: 0; padding: 0; }
  html, body { width: 1200px; height: 780px; overflow: hidden; background: var(--stage); }
  .stage {
    width: 1200px; height: 780px;
    display: flex; align-items: center; justify-content: center; gap: 36px;
  }
  .card {
    position: relative;
    width: 560px; height: 320px;
    background: var(--navy);
    border-right: 3px solid var(--gold);
    border-bottom: 3px solid var(--gold);
    overflow: hidden;
    box-shadow: 0 18px 40px rgba(0,0,0,.45);
  }

  /* Back */
  .card-back { display: flex; align-items: center; justify-content: center; }
  .back-wordmark {
    font-family: "Montserrat", sans-serif;
    font-weight: 700;
    font-size: 40px;
    letter-spacing: 4px;
    text-transform: uppercase;
    color: var(--navy-light);
  }

  /* Front */
  .gold-tab {
    position: absolute; top: 0; right: 0;
    width: 28px; height: 74px;
    background: var(--gold);
  }
  .holder { position: absolute; top: 26px; right: 48px; text-align: right; }
  .holder-name {
    font-family: "Montserrat", sans-serif; font-weight: 700;
    font-size: 30px; color: var(--gold); line-height: 1.05;
  }
  .holder-title {
    font-family: "Open Sans", sans-serif; font-size: 13px;
    color: var(--white); margin-top: 2px;
  }
  .deco-square {
    position: absolute; right: 60px; top: 118px;
    width: 150px; height: 150px;
    border: 16px solid var(--navy-light);
  }
  .brand {
    position: absolute; left: 36px; top: 96px;
    display: flex; align-items: center; gap: 10px;
    font-family: "Montserrat", sans-serif; font-weight: 700;
    font-size: 22px; letter-spacing: 2px; text-transform: uppercase;
    color: var(--white);
  }
  .brand-mark { width: 14px; height: 14px; background: var(--white); }
  .contact {
    position: absolute; left: 36px; bottom: 30px;
    font-family: "Open Sans", sans-serif; font-size: 13px;
    color: var(--white); line-height: 1.55;
  }
  .address { margin-bottom: 14px; }
  .contact-list { list-style: none; }
  .contact-list li { display: flex; align-items: center; gap: 9px; }
  .contact-list svg { width: 13px; height: 13px; flex: none; }
</style>
</head>
<body>
<main class="stage">
  <section class="card card-back" aria-label="Card back">
    <span class="back-wordmark">Harbor Crestline</span>
  </section>

  <section class="card card-front" aria-label="Card front">
    <div class="gold-tab"></div>
    <div class="holder">
      <div class="holder-name">Dorian Fenwick</div>
      <div class="holder-title">CEO/Founder</div>
    </div>
    <div class="deco-square"></div>

    <div class="brand"><span class="brand-mark"></span>Harbor Crestline</div>

    <div class="contact">
      <p class="address">4120 Meridian Ave<br>Suite 210, Lakeford, MD 20914</p>
      <ul class="contact-list">
        <li>
          <svg viewBox="0 0 24 24" fill="#c9a24a" aria-hidden="true"><path d="M6.6 10.8a15 15 0 0 0 6.6 6.6l2.2-2.2a1 1 0 0 1 1-.25 11.4 11.4 0 0 0 3.6.57 1 1 0 0 1 1 1V20a1 1 0 0 1-1 1A17 17 0 0 1 3 4a1 1 0 0 1 1-1h3.5a1 1 0 0 1 1 1c0 1.25.2 2.46.57 3.6a1 1 0 0 1-.25 1z"/></svg>
          (833) HarbCre / (833) 427-2731
        </li>
        <li>
          <svg viewBox="0 0 24 24" fill="none" stroke="#c9a24a" stroke-width="2" aria-hidden="true"><circle cx="12" cy="12" r="9"/><path d="M3 12h18M12 3c3 3.5 3 14.5 0 18M12 3c-3 3.5-3 14.5 0 18"/></svg>
          www.theharborcrestline.com
        </li>
        <li>
          <svg viewBox="0 0 24 24" fill="none" stroke="#c9a24a" stroke-width="2" aria-hidden="true"><rect x="3" y="5" width="18" height="14" rx="1"/><path d="M3 6l9 7 9-7"/></svg>
          dorian@theharborcrestline.com
        </li>
      </ul>
    </div>
  </section>
</main>
</body>
</html>
```